LinkedIn Banner Design for B2B Consulting Firm

Take the already developed logo (attached) and incorporate it into a creative banner design for placement on LinkedIn (the social media platform targeting business users). The banner will be used on the firm's company profile page on LinkedIn (not yet created).

```html
<!DOCTYPE html>
<html lang="en">
<head>
<meta charset="utf-8">
<title>Corporate Fractional Marketing Services – Profile Banner</title>
<link rel="stylesheet" href="https://fonts.googleapis.com/css2?family=Poppins:wght@300;600;700&display=swap">
<style>
  :root {
    --page-bg: #ffffff;
    --banner-deep: #14261c;
    --banner-mid: #1f3a2a;
    --accent-green: #86bb98;
    --headline-white: #ffffff;
    --photo-light: #c9d0cf;
    --photo-mid: #8e9a98;
    --photo-dark: #3c4744;
  }
  * { box-sizing: border-box; margin: 0; padding: 0; }
  html, body {
    width: 1200px;
    height: 1144px;
    overflow: hidden;
    background: var(--page-bg);
  }
  .canvas {
    position: relative;
    width: 1200px;
    height: 1144px;
  }
  .banner {
    position: absolute;
    left: 0;
    top: 470px;
    width: 1200px;
    height: 203px;
    overflow: hidden;
    background: var(--banner-deep);
  }
  .banner-backdrop {
    position: absolute;
    inset: 0;
    background:
      linear-gradient(90deg, rgba(20,38,28,0.95) 0%, rgba(31,58,42,0.85) 35%, rgba(20,38,28,0.95) 70%, var(--banner-deep) 100%),
      repeating-linear-gradient(90deg, rgba(255,255,255,0.03) 0 40px, rgba(0,0,0,0.06) 40px 90px);
  }
  .banner-photos {
    position: absolute;
    inset: 0;
  }
  .headline {
    position: absolute;
    left: 242px;
    top: 50px;
    font-family: "Poppins", sans-serif;
    line-height: 1;
  }
  .headline-lead {
    display: block;
    font-weight: 700;
    font-size: 33px;
    letter-spacing: 0.5px;
    color: var(--accent-green);
  }
  .headline-main {
    display: block;
    margin-top: 4px;
    font-weight: 300;
    font-size: 34px;
    color: var(--headline-white);
  }
  .headline-sub {
    display: block;
    margin-top: 4px;
    font-weight: 600;
    font-size: 21px;
    letter-spacing: 7.2px;
    color: var(--accent-green);
  }
</style>
</head>
<body>
  <main class="canvas">
    <section class="banner" aria-label="Company profile banner">
      <div class="banner-backdrop" role="img" aria-label="Dark green tinted photo of business people silhouetted in an office"></div>

      <svg class="banner-photos" width="1200" height="203" viewBox="0 0 1200 203" aria-hidden="false">
        <defs>
          <linearGradient id="photo-tone-a" x1="0" y1="0" x2="0" y2="1">
            <stop offset="0" stop-color="var(--photo-light)"/>
            <stop offset="0.6" stop-color="var(--photo-mid)"/>
            <stop offset="1" stop-color="var(--photo-dark)"/>
          </linearGradient>
          <linearGradient id="photo-tone-b" x1="0" y1="0" x2="1" y2="1">
            <stop offset="0" stop-color="#d4dad8"/>
            <stop offset="0.5" stop-color="#9aa5a2"/>
            <stop offset="1" stop-color="#4a5350"/>
          </linearGradient>
        </defs>
        <polygon role="img" aria-label="Office photo: lounge area with sofa and plants"
                 points="700,167 792,17 917,17 827,167" fill="url(#photo-tone-a)"/>
        <polygon role="img" aria-label="Office photo: colleagues meeting at a desk"
                 points="816,191 910,40 1036,40 945,191" fill="url(#photo-tone-b)"/>
        <polygon role="img" aria-label="Office photo: person working at a computer by the window"
                 points="942,170 1053,19 1175,19 1084,170" fill="url(#photo-tone-a)"/>
      </svg>

      <h1 class="headline">
        <span class="headline-lead">BEST-IN-CLASS</span>
        <span class="headline-main">CORPORATE FRACTIONAL</span>
        <span class="headline-sub">MARKETING SERVICES</span>
      </h1>
    </section>
  </main>
</body>
</html>
```